Heron Property Inspection business card

I am the principal inspector of Heron Property Inspections. I serve Northern Virginia from Winchester to Arlington.Associate, Federated Guild of Dwelling Examiners (FGDE)Graduate, FGDE Home Inspectors CourseNational Association of Home Inspectors ExamI'd like the business card to look more professional than comical.I pulled the attached picture off the web. I'd like to have something like that or an image of a house as my logo on the cards.

Target Market(s)

Persons who recently purchased a home.

Industry/Entity Type

Business

Contact Information for Business Card

Bob AllenBadger Home Inspections, LLC.4455 River RoadBluemont, Virginia 20135cell: 703-231-6680e-mail: tkmarlow@postvale.net

Font styles to use
Serif
Sans Serif

Requirements
Must have
• I'd like to have a logo, something that identifies me as a home inspector. The attached images are something that I'd like to have incorporated into my business card logo.
Nice to have
• I'd like a sketch of a house and/or a magnifying glass showing a house being inspected. The attached images are used as a suggestion only, I do not own the images.
Should not have
• Gimmicky stuff. I want to appear professional and trustworthy.

```html
<!DOCTYPE html>
<html lang="en">
<head>
<meta charset="utf-8">
<title>Heron Property Inspections – Business Card</title>
<link href="https://fonts.googleapis.com/css2?family=Arimo:wght@400;700&family=Didact+Gothic&display=swap" rel="stylesheet">
<style>
  :root {
    --navy: #1f4596;
    --navy-dark: #183a82;
    --sky: #2a9ad1;
    --ink: #3a3a3c;
    --rule: #4a4d55;
    --paper: #f7f7f6;
    --backdrop: #e6e3de;
  }
  html, body {
    margin: 0;
    width: 1200px;
    height: 892px;
    overflow: hidden;
    background: var(--backdrop);
  }
  .card {
    position: absolute;
    left: 100px;
    top: 160px;
    width: 1000px;
    height: 572px;
    background: var(--paper);
    box-shadow: 0 10px 30px rgba(0,0,0,0.18);
    overflow: hidden;
  }
  .band {
    position: absolute;
    left: 0;
    right: 0;
    background: linear-gradient(180deg, var(--navy) 0%, var(--navy-dark) 100%);
  }
  .band--top { top: 0; height: 52px; }
  .band--bottom { bottom: 0; height: 84px; }
  .rule {
    position: absolute;
    left: 0;
    right: 0;
    height: 3px;
    background: var(--rule);
  }
  .rule--top { top: 60px; }
  .rule--bottom { bottom: 92px; }

  .contact {
    position: absolute;
    left: 172px;
    top: 168px;
    color: var(--ink);
    font-family: "Arimo", sans-serif;
  }
  .contact__name {
    margin: 0;
    font-family: "Didact Gothic", sans-serif;
    font-size: 40px;
    font-weight: 400;
    color: var(--sky);
    line-height: 1;
  }
  .contact__role {
    margin: 2px 0 0 0;
    font-size: 20px;
    color: var(--ink);
  }
  .contact__list {
    list-style: none;
    margin: 28px 0 0 0;
    padding: 0;
  }
  .contact__item {
    display: flex;
    align-items: center;
    gap: 14px;
    font-size: 26px;
    line-height: 34px;
  }
  .contact__icon { width: 26px; height: 26px; flex: none; }
  .contact__address {
    margin: 2px 0 0 -22px;
    font-size: 21px;
    font-style: italic;
    line-height: 24px;
  }

  .brand {
    position: absolute;
    left: 600px;
    top: 340px;
    display: flex;
    align-items: center;
    gap: 14px;
    font-family: "Arimo", sans-serif;
    font-weight: 400;
    color: var(--navy);
  }
  .brand__mark {
    width: 26px;
    height: 26px;
    background: var(--navy);
    flex: none;
  }
  .brand__name {
    font-size: 28px;
    line-height: 1;
    white-space: nowrap;
  }
</style>
</head>
<body>
  <article class="card">
    <div class="band band--top"></div>
    <div class="rule rule--top"></div>

    <section class="contact">
      <h1 class="contact__name">Employee Name</h1>
      <p class="contact__role">Your Position</p>
      <ul class="contact__list">
        <li class="contact__item">
          <svg class="contact__icon" viewBox="0 0 28 28" aria-hidden="true">
            <rect width="28" height="28" fill="#1f4596"/>
            <rect x="9" y="4" width="10" height="20" rx="2" fill="none" stroke="#fff" stroke-width="2"/>
            <rect x="11" y="7" width="6" height="6" fill="#fff"/>
          </svg>
          <span>703-555-0192</span>
        </li>
        <li class="contact__item">
          <svg class="contact__icon" viewBox="0 0 28 28" aria-hidden="true">
            <rect width="28" height="28" fill="#1f4596"/>
            <rect x="5" y="8" width="18" height="12" fill="none" stroke="#fff" stroke-width="2"/>
            <path d="M5 8 L14 15 L23 8" fill="none" stroke="#fff" stroke-width="2"/>
          </svg>
          <span>tkmarlow@postvale.net</span>
        </li>
      </ul>
      <p class="contact__address">7182 Quarry Lane, Fernhill,<br>Virginia 20148</p>
    </section>

    <div class="brand">
      <div class="brand__mark"></div>
      <div class="brand__name">Heron Property Inspections</div>
    </div>

    <div class="rule rule--bottom"></div>
    <div class="band band--bottom"></div>
  </article>
</body>
</html>
```